Looking for a modern, Professional business card design

We have a simple business card, but are looking for a more modern, professional look. A sample of the basic card is attached as well as the logo. We would also like to add that we offer:
Struggling with your finances?
- Learn to become debt free
- Discover the power of cash
- Control your money instead of it controlling you
Let us help you achieve a new level of financial freedom!
Also, we would like to have a "SPECIAL OFFER!: FREE 30 minute consultation"
Financial Planning

```html
<!DOCTYPE html>
<html lang="en">
<head>
<meta charset="utf-8">
<title>Steady Ledger Coaching – Business Card</title>
<link rel="stylesheet" href="https://fonts.googleapis.com/css2?family=Roboto:wght@400;500;700&family=Roboto+Condensed:wght@700&display=swap">
<style>
  :root {
    --backdrop: #3a3a3c;
    --card-white: #ffffff;
    --card-tint: #f1f3f0;
    --card-black: #0b0b0b;
    --ink: #2b2b2b;
    --ink-soft: #555555;
    --green: #5c9e3c;
    --green-bright: #7cc242;
    --on-dark: #e8e8e8;
    --on-dark-soft: #b5b5b5;
  }
  * { box-sizing: border-box; margin: 0; padding: 0; }
  html, body { width: 1200px; height: 950px; overflow: hidden; }
  body {
    background: var(--backdrop);
    font-family: "Roboto", Arial, sans-serif;
    position: relative;
  }
  .card {
    position: absolute;
    left: 250px;
    width: 700px;
    height: 400px;
    border-radius: 4px;
    box-shadow: 0 8px 24px rgba(0,0,0,.35);
    overflow: hidden;
  }
  /* Back side */
  .card-back {
    top: 55px;
    background: linear-gradient(120deg, #1a1a1a 0%, var(--card-black) 55%, #141414 100%);
    color: var(--on-dark);
    text-align: center;
    padding-top: 60px;
  }
  .card-back .mark-dot { display: block; margin: 0 auto 34px; }
  .back-heading {
    font-family: "Roboto Condensed", "Arial Narrow", sans-serif;
    font-size: 26px;
    letter-spacing: .5px;
    margin-bottom: 16px;
  }
  .back-points {
    font-size: 16px;
    line-height: 1.6;
    color: var(--on-dark-soft);
    list-style: none;
  }
  .back-points li { display: inline; }
  .back-points li + li::before { content: " • "; color: var(--green-bright); }
  .back-invite { font-size: 16px; color: var(--on-dark-soft); margin-top: 4px; }
  .back-offer { font-size: 20px; font-weight: 700; margin-top: 22px; }
  .back-offer .offer-label { color: var(--green-bright); }

  /* Front side */
  .card-front {
    top: 495px;
    background: linear-gradient(135deg, var(--card-white) 40%, var(--card-tint) 100%);
    color: var(--ink);
  }
  .card-front .faint-disc { position: absolute; right: 70px; top: 90px; }
  .brand { position: absolute; left: 48px; top: 52px; display: flex; align-items: center; gap: 14px; }
  .brand-name {
    font-family: "Roboto Condensed", "Arial Narrow", sans-serif;
    font-size: 36px;
    color: var(--ink);
    letter-spacing: .5px;
    text-transform: uppercase;
    line-height: 1.05;
  }
  .brand-tagline {
    position: absolute; left: 110px; top: 132px;
    font-size: 12px; color: var(--ink-soft); font-style: italic;
  }
  .contact {
    position: absolute; left: 48px; top: 208px;
    font-size: 18px; line-height: 1.5; color: var(--ink-soft);
    font-style: normal;
  }
  .contact .label { color: var(--green); font-weight: 700; }
  .person { position: absolute; right: 52px; bottom: 48px; text-align: right; }
  .person-name { font-size: 24px; font-weight: 500; color: var(--green); }
  .person-role { font-size: 18px; color: var(--ink); margin-top: 2px; }
</style>
</head>
<body>

<section class="card card-back" aria-label="Card back">
  <svg class="mark-dot" width="60" height="60" viewBox="0 0 60 60" aria-hidden="true">
    <circle cx="30" cy="30" r="28" fill="#d9d9d9"/>
  </svg>
  <h2 class="back-heading">STRUGGLING WITH YOUR FINANCES?</h2>
  <ul class="back-points">
    <li>Learn to become debt free</li>
    <li>Discover the power of cash</li>
  </ul>
  <ul class="back-points">
    <li>Control your money instead of it controlling you</li>
  </ul>
  <p class="back-invite">Let us help you achieve a new level of financial freedom!</p>
  <p class="back-offer"><span class="offer-label">SPECIAL OFFER!</span> FREE 30 minute consultation</p>
</section>

<section class="card card-front" aria-label="Card front">
  <svg class="faint-disc" width="220" height="220" viewBox="0 0 220 220" aria-hidden="true">
    <circle cx="110" cy="110" r="108" fill="#5c9e3c" fill-opacity="0.07"/>
  </svg>

  <div class="brand">
    <svg width="46" height="46" viewBox="0 0 46 46" aria-hidden="true">
      <circle cx="23" cy="23" r="22" fill="#7cc242"/>
    </svg>
    <span class="brand-name">Steady Ledger<br>Coaching</span>
  </div>
  <p class="brand-tagline">Achieve a new level of personal freedom</p>

  <address class="contact">
    <div><span class="label">Mob:</span> (555) 014-2378</div>
    <div>daniel@steadyledgercoach.com</div>
    <div>www.steadyledgercoach.com</div>
  </address>

  <div class="person">
    <p class="person-name">Daniel R. Hayes</p>
    <p class="person-role">Personal Financial Coach</p>
  </div>
</section>

</body>
</html>
```